Business Card Design for Marketing Firm

Looking for business card design for higher end marketing firm. Clean but impressionable/trendy. We are a marketing firm that represents manufacturers in the foodservice equipment and supply industry. Our customers are end users such has hotels, restaurants, country clubs, convention centers and casinos as well as distributors of restaurants supplies and equipment, and manufacturers of foodservice equipment and supplies.
Target Market(s)
Hotels, Restaurants, Supply & Equipment Distributors, Foodservice Manufacturers
Industry/Entity Type
Foodservice/Hospitality
Contact Information for Business Card
Name, Title, Contact Number, Email, Website, Social Media, Address
Requirements
Must have
- Clean & Simple but Serious and Impressionable

```html
<!DOCTYPE html>
<html lang="en">
<head>
<meta charset="utf-8">
<title>Meridian Hospitality Reps – Business Card</title>
<link rel="stylesheet" href="https://fonts.googleapis.com/css2?family=Marcellus&family=Open+Sans:wght@400;700&display=swap">
<style>
  :root {
    --navy: #2a2872;
    --white: #ffffff;
    --ink: #2b2b2b;
    --stage: #ecebe8;
    --rule-light: rgba(255,255,255,0.95);
  }
  * { box-sizing: border-box; margin: 0; padding: 0; }
  html, body { width: 1200px; height: 834px; overflow: hidden; }
  body {
    background: var(--stage);
    font-family: "Open Sans", sans-serif;
    position: relative;
  }
  .card {
    position: absolute;
    top: 268px;
    width: 520px;
    height: 297px;
    overflow: hidden;
    box-shadow: 0 6px 18px rgba(0,0,0,0.18);
  }

  /* Front: contact side */
  .card--front { left: 50px; background: var(--white); }
  .front__brand {
    position: absolute; left: 30px; top: 30px; width: 186px;
    font-family: "Marcellus", serif; color: var(--navy);
  }
  .front__brand-name {
    font-size: 13px; letter-spacing: 0.3px; white-space: nowrap;
    border-bottom: 1px solid var(--navy); padding-bottom: 2px;
  }
  .front__brand-sub { font-size: 8px; text-align: right; margin-top: 1px; letter-spacing: 0.5px; }
  .front__address {
    position: absolute; left: 44px; top: 86px;
    font-size: 12.5px; line-height: 1.45; color: var(--ink);
  }
  .front__contacts {
    position: absolute; left: 30px; top: 168px; list-style: none;
    font-size: 12.5px; line-height: 1.5; color: var(--ink);
  }
  .front__contacts li { display: flex; align-items: center; gap: 6px; }
  .front__contacts svg { width: 11px; height: 11px; flex: none; }
  .front__person { position: absolute; right: 44px; top: 212px; }
  .front__name {
    font-weight: 700; font-size: 19px; color: var(--navy); letter-spacing: 0.4px;
  }
  .front__title { font-size: 13px; color: var(--ink); margin-top: 2px; }
  .front__tab {
    position: absolute; right: 0; top: 252px; width: 24px; height: 45px;
    background: var(--navy);
  }

  /* Back: brand side */
  .card--back { left: 630px; background: var(--navy); color: var(--white); }
  .back__brand {
    position: absolute; left: 36px; top: 112px; width: 420px;
    font-family: "Marcellus", serif;
  }
  .back__brand-name {
    font-size: 29px; letter-spacing: 0.8px; white-space: nowrap;
    padding-bottom: 6px; border-bottom: 1.5px solid var(--rule-light);
  }
  .back__brand-sub { font-size: 24px; text-align: right; margin-top: 2px; letter-spacing: 1px; }
  .back__social {
    position: absolute; left: 96px; top: 172px; display: flex; gap: 3px;
  }
  .back__social span {
    width: 13px; height: 13px; border-radius: 50%;
    border: 1.2px solid var(--white);
  }
</style>
</head>
<body>
  <section class="card card--front" aria-label="Business card front">
    <div class="front__brand">
      <div class="front__brand-name">MERIDIAN HOSPITALITY</div>
      <div class="front__brand-sub">REPS</div>
    </div>
    <p class="front__address">Your address, City<br>State, Zip 1234</p>
    <ul class="front__contacts">
      <li>
        <svg viewBox="0 0 12 12" aria-hidden="true"><path fill="var(--navy)" d="M2.4 1h2l1 2.6-1.3.9a6.4 6.4 0 0 0 3.4 3.4l.9-1.3 2.6 1v2c0 .8-.6 1.4-1.4 1.4A9.6 9.6 0 0 1 1 2.4C1 1.6 1.6 1 2.4 1z"/></svg>
        123 456 789
      </li>
      <li>
        <svg viewBox="0 0 12 12" aria-hidden="true"><rect x="1" y="2.5" width="10" height="7" rx="1" fill="none" stroke="var(--navy)" stroke-width="1.3"/><path d="M1.5 3l4.5 3.5L10.5 3" fill="none" stroke="var(--navy)" stroke-width="1.3"/></svg>
        info@meridianreps.com
      </li>
      <li>
        <svg viewBox="0 0 12 12" aria-hidden="true"><circle cx="6" cy="6" r="4.8" fill="none" stroke="var(--navy)" stroke-width="1.2"/><path d="M1.2 6h9.6M6 1.2c-2.4 2.6-2.4 7 0 9.6M6 1.2c2.4 2.6 2.4 7 0 9.6" fill="none" stroke="var(--navy)" stroke-width="1"/></svg>
        www.meridianreps.com
      </li>
    </ul>
    <div class="front__person">
      <div class="front__name">DANIEL REED</div>
      <div class="front__title">Managing Director</div>
    </div>
    <div class="front__tab"></div>
  </section>

  <section class="card card--back" aria-label="Business card back">
    <div class="back__brand">
      <div class="back__brand-name">MERIDIAN HOSPITALITY</div>
      <div class="back__brand-sub">REPS</div>
    </div>
    <div class="back__social" aria-label="Social media links">
      <span></span><span></span><span></span><span></span><span></span>
    </div>
  </section>
</body>
</html>
```